Professional Vehicle Wrap Design | 2020 Bexon Corvale | RV Tolk

We are seeking a full van wrap design for a 2020 Bexon Corvale K-300 Cargo Van that will represent RV Tolk. The primary color for this wrap should be sky blue to align with their branding and create a bold, professional appearance that stands out on the road.

Vehicle Details:

2020 Bexon Corvale K-300

Low Roof

129.9" Wheelbase (Regular)

Cargo configuration with sliding door on the right and dual rear doors (no side windows)

Design Requirements:

The wrap should feature sky blue as the dominant color.

Incorporate the RV Tolk logo and branding elements (logo files provided).

Design should be clean, professional, and highly visible for branding impact.

Avoid placing important text or graphics across sliding doors, seams, or complex panel curves to ensure durability and readability.

The design should complement the cargo van’s panel layout and utilize the full available wrap area effectively.

Included Files:
Download all project assets here: https://www.filevaultia.test/share/q8rk2mzn4tpw7vbd1xcl/KpZeRt73muLqwnYbHsAFcVe?key=x714nm3pqdzt2wbk9s6yr&v=htzp4qme&dl=0

We look forward to seeing creative and impactful wrap designs that help RV Tolk stand out.
*Final Files must be exported on the template provided
https://www.rvtolk.test/

Target Market(s)

RV Tolk serves homeowners, businesses, and property managers in Florence, AL. The wrap should convey professionalism and reliability to attract local clients seeking quality contracting and HVAC services.

Industry/Entity Type

RV Tolk operates in the HVAC and general contracting industry, providing heating, ventilation, and air conditioning services.

Colors

Designer to choose colors to be used in the design.

Requirements
Must have
• The wrap must feature sky blue as the primary color and prominently display the RV Tolk logo. The design should be bold, professional, and clean, avoiding critical text or graphics on sliding doors and seams. It should effectively use the full cargo van wrap area and ensure high visibility and easy brand recognition on the road.
Nice to have
• It would be great if the design incorporates subtle icons or visuals representing RV Tolk’s services, uses complementary colors to enhance the sky blue, and includes space for contact information without cluttering the overall look.
Should not have
• The design should not include overly busy patterns or small text that’s hard to read from a distance. Avoid placing important information over sliding door seams or complex curves, and steer clear of colors that clash with the primary sky blue.

```html
<!DOCTYPE html>
<html lang="en">
<head>
<meta charset="utf-8">
<title>RV Tolk – Bexon Corvale K-300 Van Wrap</title>
<link href="https://fonts.googleapis.com/css2?family=Montserrat:wght@600;700;800&display=swap" rel="stylesheet">
<style>
  :root {
    --sky: #0099dd;
    --navy: #0b3c8c;
    --red: #f43a3c;
    --light-blue: #5bc4e8;
    --white: #ffffff;
    --badge-dark: #2a2f36;
    --page: #ffffff;
  }
  html, body {
    margin: 0;
    padding: 0;
    width: 1200px;
    height: 2580px;
    overflow: hidden;
    background: var(--page);
    font-family: "Montserrat", Arial, sans-serif;
  }
  .sheet { position: relative; width: 1200px; height: 2580px; }
  .wrap-panel { position: absolute; display: block; }
  .side-view   { left: 48px;  top: 120px;  width: 1102px; height: 440px; }
  .rear-view   { left: 253px; top: 640px;  width: 692px;  height: 505px; }
  .side-print  { left: 48px;  top: 1320px; width: 1102px; height: 440px; }
  .rear-print  { left: 253px; top: 1890px; width: 692px;  height: 505px; }
  .brand-name { font-weight: 800; fill: var(--navy); letter-spacing: 1px; }
  .brand-tag  { font-weight: 700; fill: var(--light-blue); }
  .brand-sub  { font-weight: 700; fill: var(--light-blue); }
  .phone { font-weight: 700; fill: var(--white); }
  .phone-outlined { stroke: var(--navy); stroke-width: 5px; paint-order: stroke; }
  .web { font-weight: 700; fill: var(--white); }
  .service { font-weight: 700; fill: var(--white); }
  .tick-ring { fill: none; stroke: var(--white); stroke-width: 1.6; }
  .tick-mark { fill: none; stroke: var(--white); stroke-width: 1.8; stroke-linecap: round; stroke-linejoin: round; }
</style>
</head>
<body>
<div class="sheet">

  <svg width="0" height="0" style="position:absolute" aria-hidden="true">
    <defs>
      <!-- 24/7 service badge as a plain emblem shape -->
      <symbol id="service-badge" viewBox="0 0 150 110">
        <polygon points="75,0 150,55 75,110 0,55" fill="var(--red)"/>
        <polygon points="75,10 138,55 75,100 12,55" fill="var(--white)"/>
        <rect x="4" y="30" width="142" height="50" rx="4" fill="var(--badge-dark)"/>
        <rect x="10" y="36" width="130" height="38" rx="3" fill="var(--white)"/>
        <rect x="16" y="42" width="118" height="26" rx="2" fill="var(--badge-dark)"/>
      </symbol>

      <!-- Side wrap artwork -->
      <symbol id="side-art" viewBox="0 0 1102 440">
        <rect width="1102" height="440" fill="var(--sky)"/>
        <path d="M400 0 C300 80 310 240 470 300 C620 355 900 330 1102 250 L1102 0 Z" fill="var(--white)"/>
        <path d="M480 0 C400 60 400 200 520 250 C440 190 470 70 560 0 Z" fill="var(--red)"/>
        <path d="M1050 0 L1102 0 L1102 70 C1090 40 1072 18 1050 0 Z" fill="var(--red)"/>
        <path d="M600 300 C780 320 960 290 1102 195 L1102 235 C960 320 770 340 600 300 Z" fill="var(--red)"/>
        <path d="M615 252 L990 248 C960 280 900 300 850 306 L615 306 Z" fill="var(--navy)"/>

        <text class="brand-tag" x="990" y="112" font-size="24" text-anchor="end">Heating &amp; Air</text>
        <circle cx="548" cy="176" r="19" fill="var(--light-blue)"/>
        <text class="brand-name" x="580" y="205" font-size="88">RV TOLK</text>
        <text class="brand-sub" x="990" y="238" font-size="24" text-anchor="end">&amp; Sons, Inc.</text>

        <use href="#service-badge" x="474" y="213" width="140" height="108"/>
        <text class="web" x="765" y="286" font-size="26" text-anchor="middle">www.rvtolk.test</text>
        <text class="phone phone-outlined" x="262" y="292" font-size="40" text-anchor="middle">(256) 555-0148</text>
      </symbol>

      <!-- Rear doors artwork -->
      <symbol id="rear-art" viewBox="0 0 692 505">
        <rect width="692" height="505" fill="var(--sky)"/>
        <path d="M0 0 H692 V300 C560 215 420 200 300 200 C170 200 70 240 0 300 Z" fill="var(--white)"/>
        <path d="M0 250 C80 215 200 195 320 195 C470 195 600 220 692 250 L692 300 C600 235 460 214 320 214 C190 214 70 250 0 300 Z" fill="var(--red)"/>

        <text class="brand-tag" x="530" y="62" font-size="20" text-anchor="end">Heating &amp; Air</text>
        <circle cx="152" cy="112" r="16" fill="var(--light-blue)"/>
        <text class="brand-name" x="180" y="138" font-size="74">RV TOLK</text>
        <text class="brand-sub" x="530" y="170" font-size="20" text-anchor="end">&amp; Sons, Inc.</text>

        <use href="#service-badge" x="97" y="172" width="122" height="94"/>

        <g class="service-list">
          <g transform="translate(125 287)"><circle class="tick-ring" r="7.5"/><path class="tick-mark" d="M-3.5 0 L-1 3 L4 -3"/></g>
          <text class="service" x="141" y="295" font-size="22">HVAC</text>
          <g transform="translate(125 317)"><circle class="tick-ring" r="7.5"/><path class="tick-mark" d="M-3.5 0 L-1 3 L4 -3"/></g>
          <text class="service" x="141" y="325" font-size="22">INSULATION</text>
          <g transform="translate(125 347)"><circle class="tick-ring" r="7.5"/><path class="tick-mark" d="M-3.5 0 L-1 3 L4 -3"/></g>
          <text class="service" x="141" y="355" font-size="22">GENERATOR</text>
          <g transform="translate(125 377)"><circle class="tick-ring" r="7.5"/><path class="tick-mark" d="M-3.5 0 L-1 3 L4 -3"/></g>
          <text class="service" x="141" y="385" font-size="22">GAS FIREPLACES</text>
        </g>

        <text class="phone" x="480" y="318" font-size="35" text-anchor="middle">(256) 555-0148</text>
        <text class="web" x="480" y="346" font-size="22" text-anchor="middle">www.rvtolk.test</text>
      </symbol>
    </defs>
  </svg>

  <svg class="wrap-panel side-view" viewBox="0 0 1102 440" role="img" aria-label="RV Tolk van wrap, driver side"><use href="#side-art"/></svg>
  <svg class="wrap-panel rear-view" viewBox="0 0 692 505" role="img" aria-label="RV Tolk van wrap, rear doors"><use href="#rear-art"/></svg>
  <svg class="wrap-panel side-print" viewBox="0 0 1102 440" role="img" aria-label="RV Tolk side wrap print layout"><use href="#side-art"/></svg>
  <svg class="wrap-panel rear-print" viewBox="0 0 692 505" role="img" aria-label="RV Tolk rear wrap print layout"><use href="#rear-art"/></svg>

</div>
</body>
</html>
```